Our company needs a Corporate Identity Package!!!

We would like to receive submissions for a corporate identity pachage including the following elements:

1. Presentation Folder
2. Product/Service Catalogue (16 A4 pages landscape but expandable)
3. Product Brochure (up to 8 A4 pages)
4. Product Flyer (2 A4 pages)
5. Business Card
6. Letterhead
7. Envelope
8. E-mail signature.

I attach a Presentation Folder that i like (geometric but also has circle). We would like to have some ideas regarding the above 7 elements including brindavex logo colors (brindavex.net).

Payment is indicative and we are planning to increase the payment now that we found out how to actually do this. You are also more than welcome to send us a message and suggest the amount of payment for your Corporate Identity elements and we will update this.

Target Market(s)

Home | Office | Life

Colors
f78f20
0555a3
9bcb3b

Requirements
Must have
• 1. Presentation Folder
• 2. Product/Service Catalogue (16 A4 pages landscape but to be easily expandable)
• 3. Product Brochure (up to 4 A4 pages but to be easily expandable )
• 4. Product Flyer (2 A4 pages)
• 5. Business Card
• 6. Letterhead
• 7. Envelope
• 8. E-mail signature.
Nice to have
• It would be nice to include design something around the cycle that communicates the best six doctors (i.e. sunshine, water, rest, air, exercise and diet) !!!

```html
<!DOCTYPE html>
<html lang="en">
<head>
<meta charset="utf-8">
<title>brindavex – Product Brochure Spreads</title>
<link rel="stylesheet" href="https://fonts.googleapis.com/css2?family=Montserrat:wght@600;700;800&family=Open+Sans:wght@400;600&display=swap">
<style>
  :root {
    --stage: #6d6d6d;
    --navy: #0c1a38;
    --white: #ffffff;
    --orange: #f78f20;
    --blue: #0555a3;
    --sky: #3fa9f5;
    --green: #9bcb3b;
    --lime: #d7e04a;
    --ink: #2a2f3a;
    --muted: #c9d0de;
    --photo-warm: #c9a58f;
    --photo-cool: #8f8a86;
  }
  * { box-sizing: border-box; margin: 0; padding: 0; }
  html, body { width: 1200px; height: 1018px; overflow: hidden; background: var(--stage); }
  .canvas { position: relative; width: 1200px; height: 1018px; overflow: hidden; font-family: "Open Sans", Arial, sans-serif; }

  .board { position: absolute; width: 214px; height: 300px; overflow: hidden; }
  .board--dark { background: var(--navy); color: var(--muted); }
  .board--light { background: var(--white); color: var(--ink); }

  .heading { position: absolute; font-family: "Montserrat", Arial, sans-serif; font-weight: 700; font-size: 12px; }
  .heading--center { left: 0; right: 0; text-align: center; color: var(--white); }
  .heading--green { color: var(--green); }
  .heading--orange { color: var(--orange); }
  .heading .arrow { color: var(--lime); font-size: 9px; margin-right: 5px; }

  .copy { position: absolute; font-size: 4.6px; line-height: 6.4px; }
  .copy p + p { margin-top: 4px; }
  .board--dark .copy { color: var(--muted); }
  .board--light .copy { color: #4a5060; }

  .label { position: absolute; font-family: "Montserrat", Arial, sans-serif; font-weight: 800; font-size: 5px; letter-spacing: .3px; text-transform: uppercase; }

  .photo { position: absolute; border-radius: 1px; }
  .photo--gym-warm { background: linear-gradient(135deg, #e6d8cc, var(--photo-warm) 55%, #6f5a52); }
  .photo--gym-cool { background: linear-gradient(135deg, #d9d4cf, var(--photo-cool) 60%, #4f4a48); }
  .photo--trainer { background: linear-gradient(160deg, #f1efec, #cdbfb6 50%, #7c6a63); }

  .brand { position: absolute; display: flex; align-items: center; gap: 3px; font-family: "Montserrat", Arial, sans-serif; font-weight: 700; color: var(--sky); }
  .brand .dot { display: block; border-radius: 50%; background: var(--orange); }
  .brand--footer { right: 14px; bottom: 10px; font-size: 6px; }
  .brand--footer .dot { width: 6px; height: 6px; }
  .brand--cover { left: 0; right: 0; top: 78px; justify-content: center; font-size: 24px; gap: 6px; }
  .brand--cover .dot { width: 20px; height: 20px; }

  .note-box { position: absolute; width: 7px; height: 7px; border: 1px solid #e7a2a2; background: var(--white); }

  .cluster {
    position: absolute; z-index: 2;
    clip-path: polygon(50% 0, 100% 25%, 100% 75%, 50% 100%, 0 75%, 0 25%);
    background: linear-gradient(135deg, var(--orange) 0%, var(--lime) 28%, var(--green) 45%, var(--sky) 68%, var(--blue) 100%);
  }
  .cluster--alt { background: linear-gradient(200deg, var(--blue) 0%, var(--sky) 30%, var(--orange) 55%, var(--green) 80%, var(--lime) 100%); }

  .seal { position: absolute; left: 63px; top: 102px; width: 60px; height: 60px; border-radius: 50%; background: var(--white); border: 4px solid var(--orange); display: flex; align-items: center; justify-content: center; font-family: "Montserrat", Arial, sans-serif; font-weight: 700; font-size: 9px; color: var(--blue); z-index: 3; }
  .footer-line { position: absolute; left: 14px; right: 14px; bottom: 10px; font-size: 4.6px; color: var(--muted); }

  svg.overlay { position: absolute; left: 0; top: 0; width: 214px; height: 300px; }
</style>
</head>
<body>
<main class="canvas">

  <!-- Row 1 -->
  <section class="board board--dark" style="left:57px;top:25px">
    <div class="brand brand--cover"><span class="dot"></span>brindavex</div>
    <h1 class="heading heading--center" style="top:160px;font-size:13px">Product Brochure</h1>
  </section>

  <section class="board board--dark" style="left:278px;top:25px">
    <h2 class="heading heading--center" style="top:68px">Our products</h2>
    <div class="copy" style="left:16px;right:18px;top:100px">
      <p>Fresh ideas for home, office and life, shaped around six simple habits that keep every day balanced and bright. Each product is built to last, easy to use and kind to the planet, so your space stays healthy all year.</p>
      <p>Each product is built to last, easy to use and kind to the planet, so your space stays healthy all year. Fresh ideas for home, office and life, shaped around six simple habits that keep every day balanced and bright.</p>
    </div>
    <span class="note-box" style="right:4px;top:150px"></span>
    <span class="note-box" style="right:4px;top:222px"></span>
  </section>

  <section class="board board--dark" style="left:499px;top:25px">
    <h2 class="heading" style="left:14px;top:48px;color:var(--white)"><span class="arrow">▶</span>Our products</h2>
    <svg class="overlay" viewBox="0 0 214 300" aria-hidden="true">
      <g fill="none" stroke-width="1.4">
        <g stroke="var(--green)">
          <polygon points="45,95 68,108 68,134 45,147 22,134 22,108"/>
          <polygon points="116,95 139,108 139,134 116,147 93,134 93,108"/>
          <polygon points="187,95 210,108 210,134 187,147 164,134 164,108"/>
        </g>
        <g stroke="var(--orange)">
          <polygon points="45,167 68,180 68,206 45,219 22,206 22,180"/>
          <polygon points="116,167 139,180 139,206 116,219 93,206 93,180"/>
          <polygon points="187,167 210,180 210,206 187,219 164,206 164,180"/>
        </g>
        <g stroke="var(--blue)">
          <polygon points="45,234 68,247 68,273 45,286 22,273 22,247"/>
          <polygon points="116,234 139,247 139,273 116,286 93,273 93,247"/>
          <polygon points="187,234 210,247 210,273 187,286 164,273 164,247"/>
        </g>
      </g>
    </svg>
  </section>

  <!-- Row 2 -->
  <section class="board board--light" style="left:57px;top:335px">
    <h2 class="heading heading--green" style="left:14px;top:22px">Health products</h2>
    <div class="copy" style="left:14px;width:118px;top:44px">
      <p>Fresh ideas for home, office and life, shaped around six simple habits that keep every day balanced and bright.</p>
    </div>
    <svg class="overlay" viewBox="0 0 214 300" aria-hidden="true">
      <g fill="none" stroke="var(--orange)" stroke-width="1.2">
        <polygon points="41,143 62,155 62,179 41,191 20,179 20,155"/>
        <polygon points="98,143 119,155 119,179 98,191 77,179 77,155"/>
        <polygon points="157,143 178,155 178,179 157,191 136,179 136,155"/>
      </g>
    </svg>
    <span class="label" style="left:14px;top:197px;color:var(--green);text-transform:none">Health products</span>
    <span class="label" style="left:72px;top:197px;color:var(--green);text-transform:none">Health products</span>
    <span class="label" style="left:131px;top:197px;color:var(--green);text-transform:none">Health products</span>
    <div class="copy" style="left:14px;width:48px;top:206px">Clean air, pure water, calm rest.</div>
    <div class="copy" style="left:72px;width:48px;top:206px">Clean air, pure water, calm rest.</div>
    <div class="copy" style="left:131px;width:48px;top:206px">Clean air, pure water, calm rest.</div>
    <div class="brand brand--footer"><span class="dot"></span>brindavex</div>
  </section>

  <section class="board board--light" style="left:278px;top:335px">
    <div class="copy" style="left:92px;width:108px;top:30px">Each product is built to last, easy to use and kind to the planet, so your space stays healthy all year.</div>
    <div class="copy" style="left:12px;width:86px;top:136px">Fresh ideas for home, office and life, shaped around six simple habits that keep every day balanced and bright.</div>
    <div class="photo photo--gym-warm" style="left:105px;top:134px;width:95px;height:57px" role="img" aria-label="Photo: group of people exercising in a bright studio"></div>
    <div class="photo photo--gym-cool" style="left:11px;top:210px;width:94px;height:56px" role="img" aria-label="Photo: woman training with dumbbells in a gym"></div>
    <div class="copy" style="left:112px;width:88px;top:214px">Move more, eat well and breathe deeply every day.</div>
    <span class="note-box" style="right:4px;top:28px"></span>
    <span class="note-box" style="right:4px;top:256px"></span>
    <div class="brand brand--footer"><span class="dot"></span>brindavex</div>
  </section>

  <section class="board board--light" style="left:499px;top:335px">
    <h2 class="heading heading--orange" style="left:14px;top:28px">Health products</h2>
    <div class="copy" style="left:14px;right:14px;top:50px">Each product is built to last, easy to use and kind to the planet, so your space stays healthy all year.</div>
    <div class="photo photo--gym-warm" style="left:12px;top:105px;width:77px;height:88px" role="img" aria-label="Photo: woman stretching during a fitness class"></div>
    <div class="copy" style="left:95px;width:40px;top:108px">Sunshine, water, rest, air, exercise and diet.</div>
    <div class="copy" style="left:14px;width:100px;top:202px">Fresh ideas for home, office and life, shaped around six simple habits that keep every day balanced and bright.</div>
    <div class="brand brand--footer"><span class="dot"></span>brindavex</div>
  </section>

  <!-- Row 3 -->
  <section class="board board--dark" style="left:57px;top:649px">
    <h2 class="heading heading--green" style="left:0;right:0;text-align:center;top:20px">Health products</h2>
    <div class="copy" style="left:14px;right:14px;top:42px">Fresh ideas for home, office and life, shaped around six simple habits that keep every day balanced and bright.</div>
    <span class="label" style="left:14px;top:128px;color:var(--orange)">Product title</span>
    <div class="copy" style="left:14px;width:95px;top:138px">Simple tools for an active, rested life.</div>
    <div class="photo photo--trainer" style="left:121px;top:109px;width:89px;height:134px" role="img" aria-label="Photo: smiling woman lifting a dumbbell"></div>
    <div class="brand brand--footer"><span class="dot"></span>brindavex</div>
  </section>

  <section class="board board--dark" style="left:278px;top:649px">
    <svg class="overlay" viewBox="0 0 214 300" aria-hidden="true">
      <g fill="none" stroke="var(--green)" stroke-width="1.3">
        <polygon points="28,46 48,57 48,81 28,92 8,81 8,57"/>
        <polygon points="28,101 48,112 48,136 28,147 8,136 8,112"/>
        <polygon points="28,156 48,167 48,191 28,202 8,191 8,167"/>
      </g>
      <g fill="var(--green)">
        <circle cx="28" cy="69" r="12"/>
        <circle cx="28" cy="124" r="12"/>
        <circle cx="28" cy="179" r="12"/>
      </g>
      <g fill="var(--white)" font-family="Open Sans, Arial, sans-serif" font-size="4.5" font-weight="600" text-anchor="middle">
        <text x="28" y="70.5">Health tip</text>
        <text x="28" y="125.5">Health tip</text>
        <text x="28" y="180.5">Health tip</text>
      </g>
    </svg>
    <div class="copy" style="left:58px;right:16px;top:60px">Sunshine, water, rest, air, exercise and diet.</div>
    <div class="copy" style="left:58px;right:16px;top:115px">Sunshine, water, rest, air, exercise and diet.</div>
    <div class="copy" style="left:58px;right:16px;top:170px">Sunshine, water, rest, air, exercise and diet.</div>
    <div class="brand brand--footer"><span class="dot"></span>brindavex</div>
  </section>

  <section class="board board--dark" style="left:499px;top:649px">
    <div class="copy" style="left:14px;width:120px;top:30px">Each product is built to last, easy to use and kind to the planet, so your space stays healthy all year.</div>
    <svg class="overlay" viewBox="0 0 214 300" aria-hidden="true">
      <circle cx="46" cy="152" r="39" fill="var(--orange)"/>
      <circle cx="118" cy="140" r="21" fill="var(--orange)"/>
      <circle cx="118" cy="190" r="21" fill="var(--blue)"/>
      <circle cx="32" cy="217" r="22" fill="var(--green)"/>
      <circle cx="77" cy="206" r="20" fill="var(--lime)"/>
    </svg>
    <span class="label" style="left:20px;top:149px;color:var(--white)">Product title</span>
    <div class="brand brand--footer"><span class="dot"></span>brindavex</div>
  </section>

  <section class="board board--dark" style="left:861px;top:649px">
    <div class="seal">brindavex</div>
    <div class="footer-line">brindavex.net · Home | Office | Life</div>
  </section>

  <!-- Geometric clusters -->
  <div class="cluster" style="left:215px;top:-12px;width:110px;height:100px" role="img" aria-label="Geometric cluster of coloured triangles"></div>
  <div class="cluster cluster--alt" style="left:5px;top:215px;width:100px;height:115px" role="img" aria-label="Geometric cluster of coloured triangles"></div>
  <div class="cluster" style="left:655px;top:-8px;width:80px;height:70px" role="img" aria-label="Geometric cluster of coloured triangles"></div>
  <div class="cluster cluster--alt" style="left:212px;top:335px;width:130px;height:120px" role="img" aria-label="Geometric cluster of coloured triangles"></div>
  <div class="cluster" style="left:640px;top:445px;width:135px;height:150px" role="img" aria-label="Geometric cluster of coloured triangles"></div>
  <div class="cluster cluster--alt" style="left:0;top:815px;width:105px;height:155px" role="img" aria-label="Geometric cluster of coloured triangles"></div>
  <div class="cluster" style="left:650px;top:688px;width:150px;height:150px" role="img" aria-label="Geometric cluster of coloured triangles"></div>
  <div class="cluster cluster--alt" style="left:830px;top:705px;width:75px;height:80px" role="img" aria-label="Geometric cluster of coloured triangles"></div>
  <div class="cluster" style="left:990px;top:690px;width:110px;height:200px" role="img" aria-label="Geometric cluster of coloured triangles"></div>

</main>
</body>
</html>
```